Brindle Haven Website design in word press

Develop great looking website home page with basic menus in Word Press. We already have a logo, so no need to re-invent that.

Target Market(s)

donors, animal owners, emergency services.

Number of Pages Required

1 page

Font styles to use
Sans Serif

Colors
ec1f27
000000
ffffff
959595

Requirements
Must have
• Fresh design in Word Press, neutral (i.e. not American looking), uses red, black and white as core colours. Needs to have menu options for about us, join us, help us, FAQs, contact us etc. Looking for a smart, modern, professional looking home page, that we can easily add pages/menu's/widgets to. Include social media buttons for facebook, twitter etc.
Nice to have
• Images (could be in colour shades) of animals in disaster i.e. search royalty free Hurricane Lorimel, Hurrican Odwin.
Should not have
• Images that breach copyright.

```html
<!DOCTYPE html>
<html lang="en">
<head>
<meta charset="utf-8">
<title>Brindle Haven – Home</title>
<link rel="stylesheet" href="https://fonts.googleapis.com/css2?family=Poppins:wght@400;500;600;700&display=swap">
<style>
:root{
  --red:#ec1f27;
  --black:#000000;
  --white:#ffffff;
  --grey:#959595;
  --ink:#333333;
  --text:#444444;
  --panel:#efefef;
  --footer:#222222;
  --hero-a:#5d7a86;
  --hero-b:#8aa3ad;
}
*{box-sizing:border-box;margin:0;padding:0}
html,body{width:1200px;height:2449px;overflow:hidden}
body{font-family:'Poppins',sans-serif;color:var(--text);background:var(--white);position:relative}
svg.ico{display:inline-block;vertical-align:middle}

/* top bar */
.topbar{position:absolute;left:0;top:0;width:1200px;height:62px;background:var(--red)}
.topbar .edge{position:absolute;left:0;top:54px;width:1200px;height:14px}
.topbar .mail{position:absolute;left:135px;top:16px;color:var(--white);font-size:13px;display:flex;align-items:center;gap:8px}
.search{position:absolute;left:756px;top:12px;width:192px;height:31px;border-radius:16px;background:var(--white);display:flex;align-items:center;justify-content:space-between;padding:0 14px 0 18px;font-size:12px;color:#777}
.social{position:absolute;display:flex;gap:10px}
.topbar .social{left:980px;top:21px}
.social span{width:12px;height:12px;border-radius:50%;background:var(--white);display:block}

/* header */
.header{position:absolute;left:0;top:62px;width:1200px;height:90px;background:var(--white)}
.brand{position:absolute;left:139px;top:22px;display:flex;align-items:center;gap:10px}
.brand .mark{width:44px;height:44px;border-radius:50%;border:3px solid var(--red)}
.brand .name{font-weight:700;font-size:14px;color:var(--red);letter-spacing:.3px}
.nav{position:absolute;top:39px;left:0;width:1200px;font-size:13px;font-weight:500;color:#222}
.nav a{position:absolute;text-decoration:none;color:inherit}

/* hero */
.hero{position:absolute;left:0;top:152px;width:1200px;height:495px;background:linear-gradient(100deg,#4b6470 0%,var(--hero-a) 45%,var(--hero-b) 100%)}
.hero h1{position:absolute;left:135px;top:202px;color:var(--white);font-size:37px;line-height:48px;font-weight:700}
.dots{position:absolute;left:138px;top:386px;display:flex;gap:7px}
.dots span{width:10px;height:10px;border-radius:50%;background:var(--white)}
.dots span.on{background:none;border:2px solid var(--white)}

/* lists */
.pawlist{list-style:none}
.pawlist li{position:relative;padding-left:25px;font-size:13.5px;line-height:20px;color:var(--text);margin-bottom:13px}
.pawlist li svg{position:absolute;left:0;top:2px}
h2{font-weight:600;color:var(--ink);font-size:33px;line-height:1}
h3{font-weight:600;color:var(--ink);font-size:22px}
.more{display:inline-block;color:var(--red);font-weight:600;font-size:13.5px;text-decoration:none}
.photo{position:absolute;box-shadow:0 4px 14px rgba(0,0,0,.25)}

/* hope */
.hope{position:absolute;left:0;top:647px;width:1200px;height:457px;background:var(--white)}
.hope h2{position:absolute;left:134px;top:76px}
.hope .vision{position:absolute;left:134px;top:134px;width:520px}
.hope h3{position:absolute;left:134px;top:172px}
.hope .purpose{position:absolute;left:134px;top:215px;width:500px}
.hope .photo{left:688px;top:107px;width:380px;height:255px;background:linear-gradient(135deg,#3d6fb0,#b98a66 60%,#d7d1c8)}

/* what */
.what{position:absolute;left:0;top:1104px;width:1200px;height:464px;background:var(--panel)}
.what .scene{position:absolute;left:0;top:0;width:715px;height:464px;background:linear-gradient(160deg,#9aa38f,#5d6b4d 55%,#6d7460)}
.what .card{position:absolute;left:495px;top:42px;width:575px;height:381px;background:var(--panel);box-shadow:0 4px 18px rgba(0,0,0,.22);padding:46px 0 0 71px}
.what h2{color:var(--red);margin-bottom:32px}
.what .pawlist{width:460px}
.what .pawlist li{margin-bottom:14px}

/* how */
.how{position:absolute;left:0;top:1568px;width:1200px;height:465px;background:linear-gradient(180deg,#e8e8e6,#dcdcda)}
.how h2{position:absolute;left:134px;top:92px}
.how .pawlist{position:absolute;left:134px;top:148px;width:520px}
.how .pawlist li{margin-bottom:12px}
.how .more{position:absolute;left:134px;top:348px}
.how .photo{left:688px;top:122px;width:380px;height:255px;background:linear-gradient(135deg,#6e8494,#b8a792 55%,#7d8a80)}

/* footer */
.footer{position:absolute;left:0;top:2033px;width:1200px;height:416px;background:var(--footer);color:var(--white)}
.footer .brand{left:132px;top:58px}
.footer .brand .mark{border-color:var(--white)}
.footer .brand .name{color:var(--white)}
.footer h4{font-size:14px;font-weight:600;text-transform:uppercase;position:absolute}
.footer .follow{left:142px;top:187px}
.footer .social{left:145px;top:222px}
.footer .links-title{left:375px;top:48px}
.footer .links{position:absolute;left:378px;top:92px;list-style:none;font-size:12.5px;font-weight:500;line-height:24px}
.footer .contact-title{left:601px;top:45px}
.footer .contact{position:absolute;left:601px;top:84px;list-style:none;font-size:12.5px}
.footer .contact li{display:flex;gap:14px;align-items:flex-start;line-height:22px;margin-bottom:20px}
.footer .touch-title{left:838px;top:48px}
.footer .touch{position:absolute;left:841px;top:86px;width:240px;font-size:12.5px;font-weight:500;line-height:24px}
.form{position:absolute;left:843px;top:143px;width:216px}
.form .field{height:36px;border:1px solid #555;margin-bottom:12px;font-size:10px;padding:11px 18px;color:var(--white)}
.form .btn{height:36px;background:var(--white);color:var(--black);font-weight:700;font-size:11px;display:flex;align-items:center;justify-content:center}
.footer .rule{position:absolute;left:150px;top:2361px;width:920px;height:1px;background:#3a3a3a}
.footer .copy{position:absolute;left:0;width:1200px;top:378px;text-align:center;font-size:12px}
.footer .copy b{font-weight:600}
</style>
</head>
<body>
<svg width="0" height="0" style="position:absolute">
  <symbol id="paw" viewBox="0 0 20 20">
    <ellipse cx="10" cy="14" rx="5" ry="4.2"/>
    <ellipse cx="3.2" cy="8.2" rx="2.1" ry="2.6"/>
    <ellipse cx="7.4" cy="4.2" rx="2.1" ry="2.7"/>
    <ellipse cx="12.6" cy="4.2" rx="2.1" ry="2.7"/>
    <ellipse cx="16.8" cy="8.2" rx="2.1" ry="2.6"/>
  </symbol>
</svg>

<div class="topbar">
  <div class="mail">
    <svg class="ico" width="13" height="10" viewBox="0 0 13 10"><rect x=".5" y=".5" width="12" height="9" fill="none" stroke="#fff"/><path d="M.5 .5 6.5 5.5 12.5 .5" fill="none" stroke="#fff"/></svg>
    support@brindlehaven.org
  </div>
  <div class="search">search....
    <svg class="ico" width="13" height="13" viewBox="0 0 13 13"><circle cx="5.5" cy="5.5" r="4.2" fill="none" stroke="#ec1f27" stroke-width="1.8"/><path d="M8.6 8.6 12 12" stroke="#ec1f27" stroke-width="1.8"/></svg>
  </div>
  <div class="social" aria-label="Social links"><span></span><span></span><span></span><span></span></div>
  <svg class="edge" viewBox="0 0 1200 14" preserveAspectRatio="none"><path fill="#ec1f27" d="M0 0H1200V6L1180 9 1160 5 1140 10 1118 6 1096 11 1074 6 1050 9 1030 4 1008 10 985 6 962 11 940 5 918 9 895 6 872 11 850 5 828 10 805 6 782 9 760 4 738 10 715 6 692 11 670 5 648 9 625 6 602 11 580 5 558 10 535 6 512 9 490 4 468 10 445 6 422 11 400 5 378 9 355 6 332 11 310 5 288 10 265 6 242 9 220 4 198 10 175 6 152 11 130 5 108 9 85 6 62 11 40 5 18 10 0 6Z"/></svg>
</div>

<header class="header">
  <div class="brand"><span class="mark"></span><span class="name">BRINDLE HAVEN.NZ</span></div>
  <nav class="nav">
    <a style="left:552px">HOME</a>
    <a style="left:624px">ABOUT US</a>
    <a style="left:722px">JOIN US</a>
    <a style="left:805px">HELP US</a>
    <a style="left:898px">FAQS</a>
    <a style="left:976px">CONTACT US</a>
  </nav>
</header>

<section class="hero" role="img" aria-label="Rescue crew on a personal watercraft towing a dog on a float across flood water">
  <h1>WE ARE<br>BRINDLE HAVEN.NZ</h1>
  <div class="dots"><span class="on"></span><span></span><span></span></div>
</section>

<section class="hope">
  <h2>Our Hope</h2>
  <ul class="pawlist vision">
    <li><svg width="15" height="15" fill="#ec1f27"><use href="#paw"/></svg>An animal-inclusive and disaster resilient New Zealand.</li>
  </ul>
  <h3>Purpose</h3>
  <ul class="pawlist purpose">
    <li><svg width="15" height="15" fill="#ec1f27"><use href="#paw"/></svg>To address the significant animal welfare emergency management capability gap</li>
    <li><svg width="15" height="15" fill="#ec1f27"><use href="#paw"/></svg>To protect disaster affected animals in partnership with the community</li>
    <li><svg width="15" height="15" fill="#ec1f27"><use href="#paw"/></svg>To provide local response to support animal evacuation, sheltering and reunification.</li>
  </ul>
  <div class="photo" role="img" aria-label="Volunteers checking a dog beside a crate at an emergency shelter"></div>
</section>

<section class="what">
  <div class="scene" role="img" aria-label="People wading through a flooded residential street carrying animals"></div>
  <div class="card">
    <h2>What we do</h2>
    <ul class="pawlist">
      <li><svg width="15" height="15" fill="#ec1f27"><use href="#paw"/></svg>Promote animal-inclusive hazard mitigation, emergency preparedness and recovery</li>
      <li><svg width="15" height="15" fill="#ec1f27"><use href="#paw"/></svg>Develop and maintain a regional capability of animal emergency responders</li>
      <li><svg width="15" height="15" fill="#ec1f27"><use href="#paw"/></svg>Provide training and professional development in animal disaster management</li>
      <li><svg width="15" height="15" fill="#ec1f27"><use href="#paw"/></svg>Provide initial response to support to emergency services with the evacuation of animals and their temporary care</li>
    </ul>
    <a class="more" style="margin-top:4px">READ MORE</a>
  </div>
</section>

<section class="how">
  <h2>How we do it</h2>
  <ul class="pawlist">
    <li><svg width="15" height="15" fill="#ec1f27"><use href="#paw"/></svg>We are the leading voice for all animals affected by disaster</li>
    <li><svg width="15" height="15" fill="#ec1f27"><use href="#paw"/></svg>We act to do the right thing for the animals in a disaster management context</li>
    <li><svg width="15" height="15" fill="#ec1f27"><use href="#paw"/></svg>We develop local capacity to create animal inclusive community resilience</li>
    <li><svg width="15" height="15" fill="#ec1f27"><use href="#paw"/></svg>We hold to account those with responsibilities to protect animals from disaster</li>
  </ul>
  <a class="more">READ MORE</a>
  <div class="photo" role="img" aria-label="Man carrying a small dog through a flooded neighbourhood"></div>
</section>

<footer class="footer">
  <div class="brand"><span class="mark"></span><span class="name">BRINDLE HAVEN.NZ</span></div>
  <h4 class="follow">Follow us</h4>
  <div class="social" aria-label="Social links"><span></span><span></span><span></span><span></span></div>

  <h4 class="links-title">Links</h4>
  <ul class="links"><li>HOME</li><li>ABOUT US</li><li>JOIN US</li><li>HELP US</li><li>FAQS</li><li>CONTACT US</li></ul>

  <h4 class="contact-title">Contact us</h4>
  <ul class="contact">
    <li><svg class="ico" width="13" height="16" viewBox="0 0 13 16"><path d="M6.5 15C3 10.5 1.5 8 1.5 5.8a5 5 0 0 1 10 0C11.5 8 10 10.5 6.5 15Z" fill="none" stroke="#fff" stroke-width="1.3"/><circle cx="6.5" cy="5.8" r="1.8" fill="none" stroke="#fff" stroke-width="1.3"/></svg><span># 24, 88 Harbour Road,<br>Tauranga 3110</span></li>
    <li><svg class="ico" width="14" height="14" viewBox="0 0 14 14"><path d="M3 1 5.5 3.8 4.2 5.6C5 7.6 6.4 9 8.4 9.8L10.2 8.5 13 11 11.3 13C6 12.6 1.4 8 1 2.7Z" fill="#fff"/></svg><span>+64 7 555 0142</span></li>
    <li><svg class="ico" width="15" height="11" viewBox="0 0 15 11"><rect width="15" height="11" fill="#fff"/><path d="M0 0 7.5 6 15 0" fill="none" stroke="#222" stroke-width="1.3"/></svg><span>support@brindlehaven.org</span></li>
  </ul>

  <h4 class="touch-title">Get in touch</h4>
  <p class="touch">Lorem ipsum dolor sit amet, consectetur adipiscing</p>
  <div class="form">
    <div class="field">First Name</div>
    <div class="field">Last Name</div>
    <div class="field">Email Address</div>
    <div class="btn">SUBSCRIBE</div>
  </div>
  <div class="rule" style="top:328px"></div>
  <p class="copy">© 2018 <b>Brindlehaven</b> | All Rights Reserved</p>
</footer>
</body>
</html>
```